Business Card Design for a new Senior Concierge Business 1.3.24

I need a professional business card to handout at networking events for my senior helper business. I would like to use the logo I have uploaded. The design should be clear and easy to read and should list the following information...
Delia Parkhurst
Owner
www.HarborlightElderAides.com
Willowmere, Texas
936.482.5079
Delia@harborlightelderaides.com

Target Market(s)

Senior Citizens

Industry/Entity Type

Personal Helper/ Assisstant

Contact Information for Business Card

I have included the details in the project description box.

Font styles to use
Serif

Colors
0054AA
0677BA
7BADD7
CADEEF
E8F1F8
59FF00
82FF00
B8FF75
E3FFCB
F4FFEA
E54698
E96AAD
F1A4CE
F9D9EA
FCEFF6
6B429C
8869AF
B7A5CE
E3DAEB
F3F0F8

Requirements
Must have
• Include uploaded logo
Nice to have
• The log that has been uploaded
Should not have
• No crazy fonts

```html
<!DOCTYPE html>
<html lang="en">
<head>
<meta charset="utf-8">
<title>Harborlight Elder Aides – Business Card</title>
<link href="https://fonts.googleapis.com/css2?family=Open+Sans:wght@400;600;700&display=swap" rel="stylesheet">
<style>
  :root {
    --stage: #2a2a2c;
    --card: #222226;
    --edge: #e0185e;
    --brand: #6b55b5;
    --teal: #1a9aa0;
    --pink: #e0185e;
    --ink: #ffffff;
    --muted-mark: #36363b;
  }
  * { box-sizing: border-box; margin: 0; padding: 0; }
  html, body {
    width: 1200px; height: 779px; overflow: hidden;
    background: var(--stage);
    font-family: "Open Sans", sans-serif;
  }
  .stage {
    width: 1200px; height: 779px;
    display: flex; align-items: center; justify-content: center; gap: 40px;
  }
  .card {
    position: relative;
    width: 540px; height: 309px;
    background: var(--card);
    border: 4px solid var(--edge);
    border-radius: 22px;
    overflow: hidden;
  }
  /* back side */
  .card-back { display: flex; align-items: center; justify-content: center; }
  .back-name {
    font-size: 38px; font-weight: 600; color: var(--muted-mark);
    letter-spacing: 0.5px;
  }
  /* front side */
  .brand-name {
    position: absolute; left: 30px; top: 30px;
    font-size: 30px; font-weight: 600; color: var(--brand);
  }
  .person {
    position: absolute; right: 0; top: 100px;
    display: flex; align-items: stretch;
  }
  .person-text { text-align: right; padding-right: 10px; }
  .person-name { font-size: 28px; font-weight: 700; line-height: 1.1; }
  .person-name .first { color: var(--teal); }
  .person-name .last { color: var(--pink); }
  .person-role { font-size: 14px; color: var(--ink); margin-top: 2px; }
  .person-bar { width: 16px; background: var(--pink); }
  .contact {
    position: absolute; left: 30px; bottom: 22px;
    color: var(--ink); font-size: 15px; line-height: 1.5;
  }
  .contact .city { margin-bottom: 6px; }
  .contact-row { display: flex; align-items: center; gap: 8px; }
  .contact-row svg { width: 14px; height: 14px; fill: var(--teal); flex: none; }
</style>
</head>
<body>
<main class="stage">
  <section class="card card-back" aria-label="Card back">
    <span class="back-name">Harborlight Elder Aides</span>
  </section>

  <section class="card card-front" aria-label="Card front">
    <div class="brand-name">Harborlight Elder Aides</div>

    <div class="person">
      <div class="person-text">
        <div class="person-name"><span class="first">Delia</span> <span class="last">Parkhurst</span></div>
        <div class="person-role">Owner</div>
      </div>
      <div class="person-bar"></div>
    </div>

    <div class="contact">
      <div class="city">Willowmere, Texas</div>
      <div class="contact-row">
        <svg viewBox="0 0 24 24" aria-hidden="true"><path d="M6.6 10.8a15.1 15.1 0 0 0 6.6 6.6l2.2-2.2a1 1 0 0 1 1-.25 11.4 11.4 0 0 0 3.6.57 1 1 0 0 1 1 1V20a1 1 0 0 1-1 1A17 17 0 0 1 3 4a1 1 0 0 1 1-1h3.5a1 1 0 0 1 1 1c0 1.25.2 2.45.57 3.6a1 1 0 0 1-.25 1z"/></svg>
        <span>936.482.5079</span>
      </div>
      <div class="contact-row">
        <svg viewBox="0 0 24 24" aria-hidden="true"><path d="M12 2a10 10 0 1 0 0 20 10 10 0 0 0 0-20zm-1 17.9A8 8 0 0 1 4.1 10.9L9 15.8v1a2 2 0 0 0 2 2zm6.9-2.5A2 2 0 0 0 16 16h-1v-3a1 1 0 0 0-1-1H8v-2h2a1 1 0 0 0 1-1V7h2a2 2 0 0 0 2-2v-.4a8 8 0 0 1 2.9 12.8z"/></svg>
        <span>www.HarborlightElderAides.com</span>
      </div>
      <div class="contact-row">
        <svg viewBox="0 0 24 24" aria-hidden="true"><path d="M3 5h18a1 1 0 0 1 1 1v12a1 1 0 0 1-1 1H3a1 1 0 0 1-1-1V6a1 1 0 0 1 1-1zm9 7.2L4 7v1.4l8 5.2 8-5.2V7z"/></svg>
        <span>Delia@harborlightelderaides.com</span>
      </div>
    </div>
  </section>
</main>
</body>
</html>
```